KVR - Redesign (PSD Files Only)

Requirements for the site:

1. We need our logo recreated, please use the same design and change colors to work on a white background

2. The site is a "Wizard" based site, that takes the customer through the process of creating a unique web presence that suits there needs

3.Colors Needed - Main "Dark Blue" Secondary = "Dark Grey" -Other = "Light Grey and White"

4.We need a CRISP CLEAN DESIGN, simple design

5.Wireframes are a general layout and may be modified by you to enhance the design

6. We want a complete web 5.0 look with big buttons and text boxes

7.The more personality the better

8. Current Site brightpolehub.example

9.See attachments for wireframes

10. Designer should deliver PSD files, no coding is required

11. The portfolio wireframe, should look like the design of the artflockly portfolio template
Updates

KEEP IT SIMPLE.,.....

We like the quillmark scaffold style of designs

```html
<!DOCTYPE html>
<html lang="en">
<head>
<meta charset="utf-8">
<title>KVR - About Our Owner</title>
<link href="https://fonts.googleapis.com/css2?family=Dosis:wght@500;600;700&family=Open+Sans:ital,wght@0,400;0,600;1,400&display=swap" rel="stylesheet">
<style>
:root{
  --navy:#0b3a66;
  --navy-deep:#052d50;
  --nav-dark:#1d1d1d;
  --page-grey:#d6d6d6;
  --footer:#232323;
  --footer-strip:#1a1a1a;
  --orange:#ff8a1c;
  --orange-dark:#f56a00;
  --white:#ffffff;
  --text:#111;
}
*{margin:0;padding:0;box-sizing:border-box}
html,body{width:1200px;height:993px;overflow:hidden}
body{position:relative;background:var(--page-grey);font-family:'Open Sans',sans-serif;color:var(--text)}
.abs{position:absolute}
.hero{left:0;top:0;width:1200px;height:174px;background:radial-gradient(ellipse at 50% 100%,#0a5b8c 0%,#063c68 45%,#052c52 100%)}
.topbar{left:129px;top:0;width:943px;height:46px;background:var(--nav-dark)}
.topbar-edge{left:0;top:0;width:1200px;height:24px;background:#222}
.brand{left:150px;top:6px;font-family:'Dosis',sans-serif;font-weight:700;font-size:24px;color:var(--white);display:flex;align-items:center;gap:6px}
.brand i{width:10px;height:10px;background:var(--white);display:block}
.nav{left:221px;top:0;display:flex;height:46px;font-family:'Dosis',sans-serif;font-weight:500;font-size:22px;color:var(--white)}
.nav a{color:inherit;text-decoration:none;padding:0 13px;line-height:46px}
.nav a.active{background:#1e4d80}
.social{display:flex;gap:8px}
.social span{display:block;border-radius:50%;background:var(--white)}
.top-social{left:704px;top:10px}
.top-social span{width:26px;height:26px}
.phone{display:flex;align-items:center;gap:6px;font-family:'Dosis',sans-serif;font-weight:500;color:var(--white)}
.top-phone{left:884px;top:6px;font-size:28px}
.page-title{left:0;top:88px;width:1200px;text-align:center;font-family:'Dosis',sans-serif;font-weight:700;font-size:35px;color:var(--white);line-height:46px}
.page-title span{letter-spacing:3px;font-weight:500;margin:0 12px;vertical-align:6px;font-size:22px}
.notch{left:588px;top:162px;width:0;height:0;border-left:12px solid transparent;border-right:12px solid transparent;border-bottom:12px solid var(--white)}
.panel{left:129px;top:174px;width:943px;height:599px;background:var(--white);border-left:1px solid #bbb;border-right:1px solid #bbb}
.owner-title{left:161px;top:232px;font-size:26px;font-weight:600;color:var(--navy);letter-spacing:.3px}
.owner-rule{left:161px;top:273px;width:575px;height:3px;background:var(--navy)}
.owner-bio{left:161px;top:289px;width:580px;font-size:14px;line-height:19px}
.owner-bio p{margin-bottom:19px}
.btn{display:block;background:linear-gradient(var(--orange),var(--orange-dark));color:var(--white);font-family:'Dosis',sans-serif;font-weight:700;font-size:28px;text-align:center;line-height:55px;width:243px;height:55px;border:1px solid #e06000}
.btn-main{left:162px;top:514px}
.btn-note{left:164px;top:580px;font-size:15.5px;line-height:19px;color:var(--navy)}
.photo-frame{left:769px;top:224px;width:273px;height:383px;border:1px solid #ccc;box-shadow:0 0 3px rgba(0,0,0,.15);padding:7px;background:var(--white)}
.photo{width:100%;height:100%;background:linear-gradient(160deg,#e4e2de 0%,#cfcac4 45%,#8a8580 70%,#d9d6d2 100%)}
.info-bar{left:154px;top:659px;width:891px;height:52px;background:var(--navy-deep);display:flex;align-items:center;gap:10px;padding-left:17px;color:var(--white);font-style:italic;font-size:16px}
.footer{left:0;top:773px;width:1200px;height:220px;background:var(--footer)}
.foot-links{left:129px;top:815px;font-size:12.5px;line-height:19px;color:var(--white)}
.foot-social{left:498px;top:812px;gap:7px}
.foot-social span{width:38px;height:38px}
.foot-phone{left:498px;top:856px;font-size:26px}
.btn-foot{left:828px;top:811px}
.foot-strip{left:129px;top:897px;width:948px;height:53px;background:var(--footer-strip)}
.badge{left:129px;top:897px;width:157px;height:53px;background:#f4f4f4;display:flex}
.badge b{width:54px;background:#3a6cc4;display:block}
</style>
</head>
<body>
<div class="abs hero"></div>
<div class="abs topbar-edge"></div>
<div class="abs topbar"></div>
<div class="abs brand"><i></i>KVR</div>
<nav class="abs nav"><a href="#">Home</a><a href="#" class="active">About Us</a><a href="#">Portfolio</a><a href="#">Contact Us</a></nav>
<div class="abs social top-social" aria-label="Social links"><span></span><span></span><span></span><span></span></div>
<div class="abs phone top-phone">
  <svg width="14" height="20" viewBox="0 0 14 20"><path d="M3 1l3 0 1 5-2 1c1 3 2 5 4 7l2-1 3 4-2 2C6 19 1 10 3 1z" fill="#fff"/></svg>1800-555-0142</div>
<h1 class="abs page-title"><span>········</span>About Our Owner<span>········</span></h1>
<div class="abs notch"></div>

<main class="abs panel"></main>
<h2 class="abs owner-title">CEO - MILES CARVER</h2>
<div class="abs owner-rule"></div>
<div class="abs owner-bio">
  <p>Lorem ipsum dolor sit amet, consectetur adipiscing elit. In fermentum dolor non augue pretium egestas. Donec sem eros, tincidunt at congue ut, posuere sit amet est. Vivamus scelerisque viverra odio sit amet laoreet. Ut nec neque non justo rutrum tempor lobortis eu ante. Aliquam sagittis, nibh quis commodo auctor, risus mauris laoreet lectus, id facilisis libero odio nec enim. Sed id ligula adipiscing purus lacinia aliquet. Sed eu est non nisl vehicula bibendum congue sit amet enim. Lorem ipsum dolor sit amet, consectetur adipiscing elit. In fermentum dolor non augue pretium egestas.</p>
  <p>Donec sem eros, tincidunt at congue ut, posuere sit amet est. Vivamus scelerisque viverra odio sit amet laoreet. Ut nec neque non justo rutrum tempor lobortis eu ante. Aliquam sagittis, nibh quis commodo auctor</p>
</div>
<a class="abs btn btn-main" href="#">Request Consultant</a>
<p class="abs btn-note">Our web professionals will contact<br>you to discuss your project</p>
<div class="abs photo-frame"><div class="photo" role="img" aria-label="Portrait of the owner seated at a desk holding a pen, colourful notes on the wall behind"></div></div>
<div class="abs info-bar">
  <svg width="32" height="32" viewBox="0 0 32 32"><circle cx="16" cy="16" r="15" fill="#fff"/><circle cx="17" cy="9" r="2.4" fill="#052d50"/><path d="M14 14h5l-2 11h-4z" fill="#052d50"/></svg>
  As your full service marketing partner, we will deliver and end to end marketing solution for your business.
</div>

<footer class="abs footer"></footer>
<div class="abs foot-links">Home &nbsp;.&nbsp; About Us &nbsp;.&nbsp; Portfolio &nbsp;.&nbsp; Contact Us<br>Copyright © 2014 Kavera Studios Inc - All Right Reserved<br>www.brightpolehub.example</div>
<div class="abs social foot-social" aria-label="Social links"><span></span><span></span><span></span><span></span></div>
<div class="abs phone foot-phone">
  <svg width="14" height="20" viewBox="0 0 14 20"><path d="M3 1l3 0 1 5-2 1c1 3 2 5 4 7l2-1 3 4-2 2C6 19 1 10 3 1z" fill="#fff"/></svg>1800-555-0142</div>
<a class="abs btn btn-foot" href="#">Request Consultant</a>
<div class="abs foot-strip"></div>
<div class="abs badge" role="img" aria-label="Partner badge"><b></b></div>
</body>
</html>
```